Ridgeline Journeys business card

please see website
www.ridgelinejourneys.comau

info needed on card
Curtis Halvey
Ph
email
Adventure Riding GPS trails

please use my logo and colours off my site

Curtis Halvey
curtis@ridgelinejourneys.com

```html
<!DOCTYPE html>
<html lang="en">
<head>
<meta charset="utf-8">
<title>Ridgeline Journeys – Business Card</title>
<link rel="stylesheet" href="https://fonts.googleapis.com/css2?family=Open+Sans:ital,wght@0,400;0,600;0,700;1,400&display=swap">
<style>
  :root {
    --backdrop: #474747;
    --card: #f6f6f6;
    --ink: #1c1c1c;
    --ink-soft: #3a3a3a;
    --accent: #f3d81c;
    --accent-light: #f8e97a;
    --font-text: "Open Sans", Arial, sans-serif;
  }
  * { box-sizing: border-box; margin: 0; padding: 0; }
  html, body {
    width: 1200px; height: 750px; overflow: hidden;
    background: var(--backdrop);
    font-family: var(--font-text);
  }
  .canvas { position: relative; width: 1200px; height: 750px; }
  .card {
    position: absolute; left: 371px;
    width: 461px; height: 263px;
    background: var(--card);
    color: var(--ink);
    overflow: hidden;
  }
  .card--front { top: 99px; }
  .card--back { top: 381px; }

  .brand-emblem {
    position: absolute; left: 0; top: 0;
    width: 270px; height: 263px;
    display: block;
  }

  .contact {
    position: absolute; left: 250px; width: 218px; top: 70px;
    text-align: center;
  }
  .contact__name { font-size: 16px; font-weight: 600; margin-bottom: 9px; }
  .contact__line { font-size: 11px; line-height: 18px; color: var(--ink-soft); }

  .wordmark {
    font-weight: 700; text-transform: uppercase;
    color: var(--ink); line-height: 1.15; letter-spacing: 0.5px;
  }
  .front-brand {
    position: absolute; left: 250px; width: 218px; top: 164px;
    text-align: center;
  }
  .front-brand .wordmark { font-size: 24px; }
  .tagline {
    margin-top: 4px; font-size: 12px; font-style: italic; color: var(--ink-soft);
  }

  .back-brand {
    position: absolute; inset: 0;
    display: flex; align-items: center; justify-content: center; gap: 12px;
  }
  .back-brand__dot {
    width: 24px; height: 24px; border-radius: 50%; background: var(--accent);
  }
  .back-brand .wordmark { font-size: 22px; }
</style>
</head>
<body>
  <main class="canvas">
    <section class="card card--front">
      <svg class="brand-emblem" viewBox="0 0 270 263" role="img" aria-label="Large brand emblem area in yellow">
        <defs>
          <radialGradient id="emblemTone" cx="0.45" cy="0.6" r="0.6">
            <stop offset="0" stop-color="var(--accent)"/>
            <stop offset="1" stop-color="var(--accent-light)"/>
          </radialGradient>
        </defs>
        <circle cx="135" cy="125" r="118" fill="url(#emblemTone)"/>
      </svg>
      <div class="contact">
        <p class="contact__name">Curtis Halvey</p>
        <p class="contact__line">689 555 0142</p>
        <p class="contact__line">curtis@ridgelinejourneys.com</p>
        <p class="contact__line">www.ridgelinejourneys.comau</p>
      </div>
      <div class="front-brand">
        <p class="wordmark">Ridgeline<br>Journeys</p>
        <p class="tagline">Adventure Riding GPS trails</p>
      </div>
    </section>

    <section class="card card--back">
      <div class="back-brand">
        <span class="back-brand__dot"></span>
        <p class="wordmark">Ridgeline<br>Journeys</p>
      </div>
    </section>
  </main>
</body>
</html>
```